Marlowe Group needs a business card

I would like the card to be simple but modern and elegant.
I like black and white.
or black and gold.
we are a private finance lender and also are involved in property and property developments.

please look at the business card photos i provided i would like M.G only one one side and all the other details on the other side use fonts that tie in with my theme.

Industry/Entity Type

Finance

Contact Information for Business Card

Marlowe Group (M.G) Daniel Marlowe M: 0413586207 E: danmarl@inboxmail.test

Font styles to use
Other font styles liked:
• Use fonts that would reflect our business

Colors
000000
ffffff

Requirements
Must have
• one side of details
• other side has either M.G or Marlowe Group like in the photos provided

```html
<!DOCTYPE html>
<html lang="en">
<head>
<meta charset="utf-8">
<title>Marlowe Group — Business Card</title>
<link rel="stylesheet" href="https://fonts.googleapis.com/css2?family=Cinzel:wght@400;500&family=Open+Sans:wght@400;700&display=swap">
<style>
  :root {
    --page: #ffffff;
    --card: #000000;
    --gold: #f2c230;
    --gold-light: #fde79b;
    --gold-deep: #efc138;
    --ink: #111111;
    --white: #ffffff;
  }
  * { margin: 0; padding: 0; box-sizing: border-box; }
  html, body {
    width: 1200px; height: 900px; overflow: hidden;
    background: var(--page);
  }
  .canvas { position: relative; width: 1200px; height: 900px; }

  .card {
    position: absolute; top: 275px; width: 477px; height: 294px;
    background: var(--card); overflow: hidden;
  }
  .card--front { left: 116px; border-radius: 0 60px 0 60px; }
  .card--back  { left: 622px; border-radius: 60px 0 60px 0; }

  /* front */
  .band {
    position: absolute; top: 47px; height: 99px;
    background: linear-gradient(to bottom, var(--gold-light), var(--gold-deep));
  }
  .band--left  { left: 0; width: 42px; }
  .band--right { left: 206px; right: 0; }

  .front-mark {
    position: absolute; left: 42px; width: 164px; top: 47px; height: 99px;
    display: flex; align-items: center; justify-content: center;
    font-family: "Cinzel", serif; font-weight: 500; font-size: 52px;
    color: var(--gold); letter-spacing: 1px;
  }

  .holder-name {
    position: absolute; right: 19px; top: 84px;
    font-family: "Open Sans", sans-serif; font-weight: 700; font-size: 17px;
    color: var(--ink);
  }

  .contacts {
    position: absolute; right: 19px; top: 223px;
    list-style: none;
    font-family: "Open Sans", sans-serif; font-size: 13px; color: var(--white);
  }
  .contacts li {
    display: flex; align-items: center; justify-content: flex-end;
    gap: 8px; height: 20px;
  }
  .contacts svg { width: 10px; height: 10px; fill: var(--gold); }

  /* back */
  .back-mark {
    position: absolute; left: 0; right: 0; top: 72px;
    text-align: center;
    font-family: "Cinzel", serif; font-weight: 500; font-size: 84px;
    color: var(--gold); letter-spacing: 2px; line-height: 1;
  }
  .company-name {
    position: absolute; left: 0; right: 0; top: 205px;
    text-align: center;
    font-family: "Cinzel", serif; font-weight: 400; font-size: 22px;
    color: var(--gold); letter-spacing: 0.5px;
  }
</style>
</head>
<body>
<main class="canvas">
  <section class="card card--front" aria-label="Card front">
    <div class="band band--left"></div>
    <div class="band band--right"></div>
    <div class="front-mark">M.G</div>
    <h1 class="holder-name">Daniel Marlowe</h1>
    <ul class="contacts">
      <li>0413586207
        <svg viewBox="0 0 24 24" aria-hidden="true"><path d="M6.6 10.8a15.1 15.1 0 0 0 6.6 6.6l2.2-2.2a1 1 0 0 1 1-.25 11.4 11.4 0 0 0 3.6.57 1 1 0 0 1 1 1V20a1 1 0 0 1-1 1A17 17 0 0 1 3 4a1 1 0 0 1 1-1h3.5a1 1 0 0 1 1 1c0 1.25.2 2.45.57 3.57a1 1 0 0 1-.25 1z"/></svg>
      </li>
      <li>danmarl@inboxmail.test
        <svg viewBox="0 0 24 24" aria-hidden="true"><path d="M2 5h20v14H2z M2 5l10 8 10-8" stroke="#000" stroke-width="1.5"/></svg>
      </li>
    </ul>
  </section>

  <section class="card card--back" aria-label="Card back">
    <div class="back-mark">M.G</div>
    <p class="company-name">Marlowe Group</p>
  </section>
</main>
</body>
</html>
```